Nanny Share Ecommerce Website for Finding Childcare and Parents who need Childcare BrightPramHub.net

Our company needs an ecommerce website (BrightPramHub.net) for a US subscription based service strictly for nanny sharing that connects families and caregivers. The website would allow families to connect with one another as well as to search for nannies. The service would be searchable for other families by location (by radius or zip code), children demographic (age range/gender/special needs), days of week or times, after school care, school closure days (holidays), etc. The service would also be searchable for nannies based on gender, provider age range, years experience, language, hourly rate, transportation available, certification (CPR first aid), education etc. The search fields would be searchable and sortable and allow to connect with the provider (after paying subscription fee). The service would be similar to tendlyfolk.net in that it would allow for families and caregivers to post photos as well as a short bio of the themselves. There would also be a feedback/star rating mechanism to rate caregivers who have performed work for families (viewable to public). The service would be free for nannies to post their bios and only a subscription based service for families to connect with other families or with caregivers (able to view bio but need service to connect). There will be a short bio on the benefits of nanny sharing (reduced cost, increased flexibility for parents, reduced illness, increased socialization with other children vs. sole nanny), as well as Q&A section with best practices.

Target Market(s)

Families, Nannies

Industry/Entity Type

Childcare

Logo Text

Bright Pram Hub

Coding

Coded - Design and coding required

Number of Pages Required

5+ page

Requirements
Must have
• Searchable (need to be able to search for families as well as nannies), responsive, functional, easy to use, add value to families and nannies. Needs to be able to collect payment for subscription.
Nice to have
• Optimized for mobile, SEO optimized

```html
<!DOCTYPE html>
<html lang="en">
<head>
<meta charset="utf-8">
<title>Bright Pram Hub – Nanny Sharing</title>
<link rel="stylesheet" href="https://fonts.googleapis.com/css2?family=Lato:wght@300;400;700;900&display=swap">
<style>
:root{
  --teal:#1fd0d0;
  --teal-dark:#14b9ba;
  --ink:#1d1d1f;
  --text:#555a60;
  --muted:#8a8f95;
  --line:#dcdde0;
  --band:#f3f3f3;
  --card:#f1f1f1;
  --dark-bar:#5a5a5c;
  --footer:#2b3142;
  --white:#ffffff;
}
*{box-sizing:border-box;margin:0;padding:0}
html,body{width:1200px;height:3364px;overflow:hidden}
body{font-family:'Lato',sans-serif;color:var(--text);background:var(--white);position:relative}
a{color:inherit;text-decoration:none}

/* header */
.site-header{height:85px;display:flex;align-items:center;justify-content:space-between;padding:0 130px}
.brand{font-size:38px;font-weight:400;color:var(--ink);letter-spacing:.5px}
.header-tools{display:flex;align-items:center;gap:14px;font-size:13px}
.lang{color:var(--text);margin-right:14px}
.btn-login{border:1px solid var(--line);padding:6px 11px;color:var(--text)}
.btn-register{background:var(--teal);color:var(--white);padding:7px 16px}

/* hero */
.hero{position:relative;height:527px}
.hero-photo{position:absolute;inset:0;background:linear-gradient(90deg,#c9d6de 0%,#e8dccf 30%,#f3e6dc 55%,#e9e3de 80%,#d9dde2 100%)}
.main-nav{position:absolute;top:0;left:0;right:0;height:40px;background:rgba(255,255,255,.72);display:flex;justify-content:center;gap:62px;align-items:center;font-size:15px;color:var(--ink)}
.main-nav .active{border-bottom:2px solid var(--ink);padding-bottom:2px}
.hero-caption{position:absolute;right:133px;top:75px;text-align:right;color:#8c8f93}
.hero-caption .light{font-size:38px;font-weight:300}
.hero-caption .bold{font-size:38px;font-weight:700;letter-spacing:1px}
.hero-arrow{position:absolute;top:245px;width:40px;height:40px}
.hero-arrow.left{left:36px}.hero-arrow.right{right:36px}

/* find bar */
.find-bar{position:absolute;left:0;right:0;bottom:0;height:80px;display:flex}
.find-half{flex:0 0 600px;display:flex;align-items:center;gap:44px;padding-left:130px}
.find-half.nannies{background:rgba(31,208,208,.92);position:relative}
.find-half.job{background:rgba(80,80,82,.9);padding-left:92px}
.find-title{font-size:40px;font-weight:700;color:var(--white);letter-spacing:.5px}
.find-btn{background:var(--white);color:var(--ink);width:135px;height:45px;display:flex;align-items:center;justify-content:center;font-size:15px;letter-spacing:.5px}
.find-half.nannies::after{content:"";position:absolute;left:348px;bottom:-26px;border-left:26px solid transparent;border-right:26px solid transparent;border-top:26px solid rgba(31,208,208,.92)}

/* search */
.search{background:var(--band);height:240px;padding:55px 130px 0;position:relative}
.search-row{display:flex;gap:18px}
.field label{display:block;font-size:12px;color:var(--ink);margin-bottom:8px}
.field .input{height:40px;background:var(--white);border:1px solid var(--line);display:flex;align-items:center;justify-content:space-between;padding:0 12px;font-size:11px;color:var(--muted)}
.btn-more{position:absolute;left:552px;top:144px;width:96px;height:44px;background:var(--teal);color:var(--white);display:flex;align-items:center;justify-content:center;font-size:14px;font-weight:700}

/* services */
.services{position:relative;padding:90px 0 0;height:1019px}
.section-title{font-size:33px;font-weight:400;color:var(--ink);text-align:center}
.intro{width:940px;margin:18px auto 0;text-align:center;font-size:13px;line-height:25px}
.cards{display:flex;gap:48px;justify-content:center;margin-top:45px}
.care-card{width:444px;height:455px;background:var(--card)}
.care-photo{height:319px}
.care-photo.child{background:linear-gradient(135deg,#d8cfc2,#b7c1c8 45%,#c2426f 80%,#9a3158)}
.care-photo.companion{background:linear-gradient(135deg,#ece7df,#d7ccbd 50%,#cdb8a0)}
.care-body{padding:30px 28px}
.care-body h3{font-size:18px;font-weight:400;color:var(--ink)}
.care-tags{display:flex;gap:30px;list-style:none;font-size:11px;color:var(--muted);margin-top:12px}
.care-tags li::before{content:"";display:inline-block;width:4px;height:4px;border-radius:50%;background:var(--muted);margin-right:7px;vertical-align:middle}
.care-more{display:block;margin-top:14px;font-size:11px;font-weight:700;color:var(--ink)}
.slide-arrow{position:absolute;top:1162px;width:20px;height:30px}
.slide-arrow.left{left:46px}.slide-arrow.right{right:46px}
.benefits{margin:54px auto 0;width:936px;height:200px;border:1px solid var(--line);padding-top:38px}
.benefits h2{font-size:30px;font-weight:400;color:var(--ink);text-align:center}
.benefit-list{list-style:none;display:grid;grid-template-columns:300px 330px;column-gap:0;row-gap:14px;margin:22px 0 0 238px;font-size:14px;color:var(--ink)}
.benefit-list li{display:flex;align-items:center;gap:10px}

/* testimonials */
.testimonials{background:var(--band);height:343px;padding-top:50px;text-align:center}
.quote{width:940px;margin:20px auto 0;font-size:15px;line-height:25px}
.author{color:var(--teal-dark);font-size:15px;margin-top:12px}
.stars{margin-top:10px;letter-spacing:3px;color:#555;font-size:15px}
.dots{display:flex;gap:10px;justify-content:center;margin-top:14px}
.dots span{width:11px;height:11px;border-radius:50%;background:#c9cacc}
.dots span.on{background:var(--teal)}

/* how it works */
.how{height:489px;padding-top:75px}
.tabs{display:flex;width:482px;margin:18px auto 0;height:47px;font-size:17px}
.tab{flex:1;display:flex;align-items:center;justify-content:center;background:#f0f0f0;color:var(--muted)}
.tab.active{background:var(--teal);color:var(--white);position:relative}
.tab.active::after{content:"";position:absolute;left:50%;bottom:-14px;margin-left:-14px;border-left:14px solid transparent;border-right:14px solid transparent;border-top:14px solid var(--teal)}
.steps{display:flex;justify-content:center;gap:36px;margin-top:42px}
.step{width:157px;text-align:center;font-size:15px;color:var(--ink)}
.step-circle{width:157px;height:157px;border-radius:50%;background:#f1f1f1;border:2px solid #e3e3e3;display:flex;align-items:center;justify-content:center;margin-bottom:22px}

/* faq */
.faq{background:var(--band);height:343px;padding-top:68px;text-align:center}
.faq-q{font-size:18px;color:var(--ink);margin-top:18px}
.faq-a{width:920px;margin:10px auto 0;font-size:15px;line-height:26px}

/* cta */
.cta{height:224px;padding-top:78px;text-align:center}
.cta p{font-size:19px;color:var(--ink)}
.cta-buttons{display:flex;gap:22px;justify-content:center;margin-top:22px}
.cta-buttons a{background:var(--teal);color:var(--white);font-size:14px;font-weight:700;width:135px;height:45px;display:flex;align-items:center;justify-content:center}

/* footer */
.site-footer{background:var(--footer);height:94px;padding:26px 130px 0;color:#aeb2bb;font-size:12px;position:relative}
.footer-nav{display:flex;gap:8px}
.footer-copy{margin-top:14px}
.social{position:absolute;right:130px;top:34px;display:flex;gap:8px}
.social span{width:24px;height:24px;border-radius:50%;background:#3b5b9a}
.social span+span{background:#34a7e0}
</style>
</head>
<body>

<header class="site-header">
  <div class="brand">Bright Pram Hub</div>
  <div class="header-tools">
    <span class="lang">English &#8964;</span>
    <a class="btn-login" href="#">Login</a>
    <a class="btn-register" href="#">Register Now</a>
  </div>
</header>

<section class="hero">
  <div class="hero-photo" role="img" aria-label="Photo of a smiling mother with her young daughter in a bright living room"></div>
  <nav class="main-nav">
    <a class="active" href="#">Child care</a><a href="#">Housekeeping</a><a href="#">Testimonials</a><a href="#">How it works</a><a href="#">FAQ</a><a href="#">Support</a>
  </nav>
  <div class="hero-caption">
    <div class="light">Etiam quis</div>
    <div class="bold">ALIQUET RISUS</div>
  </div>
  <svg class="hero-arrow left" viewBox="0 0 40 40"><circle cx="20" cy="20" r="19" fill="#1fd0d0" stroke="#fff" stroke-width="2"/><path d="M23 12l-8 8 8 8" fill="none" stroke="#fff" stroke-width="3"/></svg>
  <svg class="hero-arrow right" viewBox="0 0 40 40"><circle cx="20" cy="20" r="19" fill="#1fd0d0" stroke="#fff" stroke-width="2"/><path d="M17 12l8 8-8 8" fill="none" stroke="#fff" stroke-width="3"/></svg>
  <div class="find-bar">
    <div class="find-half nannies"><span class="find-title">FIND NANNIES</span><a class="find-btn" href="#">FIND</a></div>
    <div class="find-half job"><span class="find-title">FIND A JOB</span><a class="find-btn" href="#">FIND</a></div>
  </div>
</section>

<section class="search">
  <div class="search-row">
    <div class="field" style="width:220px"><label>Choose Location</label><div class="input">by radius or zip code<svg width="10" height="13" viewBox="0 0 10 13"><path d="M5 0a5 5 0 015 5c0 3-5 8-5 8S0 8 0 5a5 5 0 015-5z" fill="#8a8f95"/><circle cx="5" cy="5" r="2" fill="#fff"/></svg></div></div>
    <div class="field" style="width:105px"><label>Children Age</label><div class="input">0 months<span>&#8964;</span></div></div>
    <div class="field" style="width:107px"><label>Children Gender</label><div class="input">Male<span>&#8964;</span></div></div>
    <div class="field" style="width:220px"><label>Any Special Needs?</label><div class="input">Choose<span>&#8964;</span></div></div>
    <div class="field" style="width:220px"><label>Days of Week or Times</label><div class="input">Choose<svg width="12" height="12" viewBox="0 0 12 12"><rect x="0.5" y="1.5" width="11" height="10" fill="none" stroke="#8a8f95"/><rect x="0.5" y="1.5" width="11" height="3" fill="#8a8f95"/></svg></div></div>
  </div>
  <a class="btn-more" href="#">MORE &#8250;</a>
</section>

<section class="services">
  <h2 class="section-title">Suspendisse gravida ornare erat</h2>
  <p class="intro">Fusce nec leo ac urna pulvinar auctor. Mauris bibendum fringilla velit. Nulla in lorem at massa pellentesque posuere. Nulla tristique posuere molestie. Aliquam erat volutpat. Etiam quis aliquet risus. Duis ornare erat eget magna dapibus, in accumsan quam pharetra. Nam tempus, quam in bibendum vulputate, sapien dolor viverra nisl, vitae euismod elit turpis et nulla. Pellentesque blandit lacus eget nunc faucibus</p>
  <div class="cards">
    <article class="care-card">
      <div class="care-photo child" role="img" aria-label="Photo of a caregiver holding a baby in a striped hat"></div>
      <div class="care-body">
        <h3>ChildCare</h3>
        <ul class="care-tags"><li>In-home care</li><li>Out-of-home care</li><li>Focused care</li></ul>
        <a class="care-more" href="#">MORE &#8250;</a>
      </div>
    </article>
    <article class="care-card">
      <div class="care-photo companion" role="img" aria-label="Photo of a smiling senior woman at home"></div>
      <div class="care-body">
        <h3>Companion care</h3>
        <ul class="care-tags"><li>Personal care</li><li>Dementia &amp; Alzheimer's</li><li>Pet Care</li></ul>
        <a class="care-more" href="#">MORE &#8250;</a>
      </div>
    </article>
  </div>
  <svg class="slide-arrow left" viewBox="0 0 20 30"><path d="M15 3L4 15l11 12" fill="none" stroke="#b5b7ba" stroke-width="2"/></svg>
  <svg class="slide-arrow right" viewBox="0 0 20 30"><path d="M5 3l11 12L5 27" fill="none" stroke="#b5b7ba" stroke-width="2"/></svg>
  <div class="benefits">
    <h2>Benefits of Nanny Sharing</h2>
    <ul class="benefit-list">
      <li><svg width="14" height="14" viewBox="0 0 14 14"><circle cx="7" cy="7" r="7" fill="#555a60"/><path d="M3.5 7l2.5 2.5 4.5-5" fill="none" stroke="#fff" stroke-width="1.6"/></svg>Reduced cost</li>
      <li><svg width="14" height="14" viewBox="0 0 14 14"><circle cx="7" cy="7" r="7" fill="#555a60"/><path d="M3.5 7l2.5 2.5 4.5-5" fill="none" stroke="#fff" stroke-width="1.6"/></svg>Reduced illness</li>
      <li><svg width="14" height="14" viewBox="0 0 14 14"><circle cx="7" cy="7" r="7" fill="#555a60"/><path d="M3.5 7l2.5 2.5 4.5-5" fill="none" stroke="#fff" stroke-width="1.6"/></svg>Increasedflexibility for parents</li>
      <li><svg width="14" height="14" viewBox="0 0 14 14"><circle cx="7" cy="7" r="7" fill="#555a60"/><path d="M3.5 7l2.5 2.5 4.5-5" fill="none" stroke="#fff" stroke-width="1.6"/></svg>Increased socialization with other children vs. sole nanny</li>
    </ul>
  </div>
</section>

<section class="testimonials">
  <h2 class="section-title">Testimonials</h2>
  <p class="quote">" Vestibulum condimentum, risus ut posuere cursus, velit justo accumsan sem, lobortis aliquet metus dui eu libero. Pellentesque a imperdiet dolor, et auctor est. Fusce sollicitudin lorem et luctus volutpat. Proin placerat dapibus gravida. In tristique tristique nulla eget hendrerit. Maecenas vel tortor accumsan quam varius imperdiet vel eget elit. "</p>
  <div class="author">Sophia, City name</div>
  <div class="stars">&#9733;&#9733;&#9733;&#9733;&#9733;</div>
  <div class="dots"><span class="on"></span><span></span><span></span><span></span></div>
</section>

<section class="how">
  <h2 class="section-title">How it works</h2>
  <div class="tabs"><div class="tab active">Find Nannies</div><div class="tab">Find a Job</div></div>
  <div class="steps">
    <div class="step"><div class="step-circle"><svg width="44" height="44" viewBox="0 0 44 44"><rect x="4" y="8" width="30" height="30" rx="3" fill="none" stroke="#8a8f95" stroke-width="3"/><path d="M18 28l2-7 16-16 5 5-16 16z" fill="#8a8f95"/></svg></div>Sign Up</div>
    <div class="step"><div class="step-circle"><svg width="36" height="44" viewBox="0 0 36 44"><path d="M2 2h22l10 10v30H2z" fill="#8a8f95"/><path d="M24 2v10h10" fill="#c8cacd"/></svg></div>Create a job</div>
    <div class="step"><div class="step-circle"><svg width="50" height="40" viewBox="0 0 50 40"><circle cx="25" cy="11" r="7" fill="#8a8f95"/><circle cx="10" cy="15" r="5" fill="#8a8f95"/><circle cx="40" cy="15" r="5" fill="#8a8f95"/><path d="M13 38c0-10 5-16 12-16s12 6 12 16z" fill="#8a8f95"/><path d="M1 36c0-8 4-13 9-13 3 0 5 1 6 3-2 3-3 6-3 10z" fill="#8a8f95"/><path d="M49 36c0-8-4-13-9-13-3 0-5 1-6 3 2 3 3 6 3 10z" fill="#8a8f95"/></svg></div>View Profiles</div>
    <div class="step"><div class="step-circle"><svg width="38" height="46" viewBox="0 0 38 46"><path d="M12 4a4 4 0 018 0v14h10a6 6 0 016 6v10c0 6-5 10-11 10h-6c-5 0-8-3-10-7L3 27l4-3 5 5z" fill="none" stroke="#8a8f95" stroke-width="3"/></svg></div>Hire a Caregiver</div>
    <div class="step"><div class="step-circle"><svg width="44" height="42" viewBox="0 0 44 42"><rect x="2" y="18" width="9" height="22" fill="#8a8f95"/><path d="M14 18l8-14c3-3 7-1 6 4l-2 9h12c3 0 5 3 4 6l-4 14c-1 2-2 3-4 3H14z" fill="#8a8f95"/></svg></div>Get your care</div>
  </div>
</section>

<section class="faq">
  <h2 class="section-title">FAQs</h2>
  <p class="faq-q">Duis hendrerit arcu ut sem egestas, vulputate porttitor neque?</p>
  <p class="faq-a">Praesent iaculis faucibus urna sit amet lacinia. Maecenas consequat justo enim, ac mattis massa imperdiet quis. Fusce eget neque elit. Sed augue orci, elementum in magna congue, tincidunt vulputate erat. Aliquam consectetur orci molestie dictum molestie. Proin eget congue nulla, vel tempor diam. Ut non ante est.</p>
  <div class="dots" style="margin-top:18px"><span class="on"></span><span></span><span></span><span></span></div>
</section>

<section class="cta">
  <p>Pellentesque convallis molestie enim sit amet efficitur. Etiam id imperdiet lectus.</p>
  <div class="cta-buttons"><a href="#">FIND NANNIES</a><a href="#">FIND A JOB</a></div>
</section>

<footer class="site-footer">
  <nav class="footer-nav"><a href="#">Child care</a>|<a href="#">Housekeeping</a>|<a href="#">Testimonials</a>|<a href="#">How it works</a>|<a href="#">FAQ</a>|<a href="#">Support</a></nav>
  <div class="footer-copy">Copyright &copy; 2018 Bright Pram Hub. All rights reserved.</div>
  <div class="social"><span></span><span></span></div>
</footer>

</body>
</html>
```